Hartwell Estates Business Cards

I would like a business card that includes myself and my partner.
Includes: Logo, office #, email, website, our names, our numbers and possibly the address. I would also like the logo to be embossed and the card to be horizontal.
There is a photo of our yard signs to give you an idea of the colors of our business.

Target Market(s)

Everyone in real estate market.
We are in a rural area. Our clientele are from all socioeconomic backgrounds.

Industry/Entity Type

Real Estate Agent

Contact Information for Business Card

Company Name: Hartwell Estates
Our Names, Titles & Cell #'s : Dana Pembrook-Broker (555).317.6624, Marla Pembrook-Realtor (555).609.1385
Office #: (555).240.3918
Website: hartwellestates-demo.com
Joint Email: pembrook@hartwellestates-demo.com
Office Address: 418B W. Calloway Ave.
Calder Springs, OK. 70913

Font styles to use
Serif

Requirements
Must have
• HORIZONTAL, Logo, Myself and my partners names, Our cell #'s, our office #, our website, our email address
Nice to have
• Embossed logo, office address, our titles.

```html
<!DOCTYPE html>
<html lang="en">
<head>
<meta charset="utf-8">
<title>Hartwell Estates Business Cards</title>
<link href="https://fonts.googleapis.com/css2?family=EB+Garamond:wght@600&family=Source+Sans+3:wght@400;600&display=swap" rel="stylesheet">
<style>
  :root {
    --stage: #ebe8e5;
    --card: #0d0d0d;
    --card-band: #1d1d1d;
    --ink: #ffffff;
    --ink-soft: #e6e6e6;
  }
  * { margin: 0; padding: 0; box-sizing: border-box; }
  html, body { width: 1200px; height: 900px; overflow: hidden; }
  body {
    position: relative;
    background: var(--stage);
    font-family: "Source Sans 3", "Helvetica Neue", Arial, sans-serif;
    color: var(--ink);
  }
  .card {
    position: absolute;
    background: var(--card);
    overflow: hidden;
    box-shadow: 0 6px 18px rgba(0,0,0,.25);
  }
  .card--front { left: 238px; top: 62px; width: 555px; height: 342px; }
  .card--back  { left: 457px; top: 518px; width: 560px; height: 344px; }

  .card__band { position: absolute; inset: 0; }

  .brand {
    position: absolute;
    display: flex;
    align-items: center;
    gap: 16px;
    font-family: "EB Garamond", Georgia, serif;
    font-weight: 600;
    color: var(--ink);
  }
  .brand__dot {
    width: 52px; height: 52px; border-radius: 50%;
    background: var(--ink);
    flex: none;
  }
  .brand__words { display: flex; flex-direction: column; align-items: center; line-height: 1; }
  .brand__name { font-size: 40px; letter-spacing: 1px; }
  .brand__rule { width: 100%; height: 1.5px; background: var(--ink); margin-top: 5px; }
  .brand__sub { font-size: 26px; margin-top: 5px; }

  .card--front .brand { left: 25px; top: 34px; }
  .card--back .brand { left: 82px; top: 115px; gap: 22px; }
  .card--back .brand__dot { width: 68px; height: 68px; }
  .card--back .brand__name { font-size: 52px; }
  .card--back .brand__rule { margin-top: 6px; }
  .card--back .brand__sub { font-size: 34px; margin-top: 6px; }

  .agent { position: absolute; left: 25px; line-height: 1.25; }
  .agent--broker { top: 145px; }
  .agent--realtor { top: 245px; }
  .agent__name { font-size: 19px; font-weight: 600; }
  .agent__title { font-size: 17px; color: var(--ink-soft); }
  .agent__cell { font-size: 15px; color: var(--ink-soft); display: flex; align-items: center; gap: 5px; }
  .icon-mobile { width: 7px; height: 11px; border: 1.5px solid var(--ink); border-radius: 1.5px; }

  .office {
    position: absolute; right: 22px; top: 248px;
    list-style: none; text-align: right;
    font-size: 15px; line-height: 20px; color: var(--ink-soft);
  }
  .office li { display: flex; justify-content: flex-end; align-items: center; gap: 6px; }
  .office svg { width: 13px; height: 13px; flex: none; }

  .address {
    position: absolute; left: 0; right: 0; top: 298px;
    text-align: center; font-size: 15px; color: var(--ink-soft);
  }
</style>
</head>
<body>

<section class="card card--front" aria-label="Card front">
  <svg class="card__band" viewBox="0 0 555 342" preserveAspectRatio="none" aria-hidden="true">
    <polygon points="462,0 555,0 555,342 217,342" fill="var(--card-band)"/>
  </svg>

  <div class="brand">
    <span class="brand__dot"></span>
    <span class="brand__words">
      <span class="brand__name">HARTWELL</span>
      <span class="brand__rule"></span>
      <span class="brand__sub">Estates</span>
    </span>
  </div>

  <div class="agent agent--broker">
    <p class="agent__name">Dana Pembrook</p>
    <p class="agent__title">Broker</p>
    <p class="agent__cell"><span class="icon-mobile"></span>(555).317.6624</p>
  </div>

  <div class="agent agent--realtor">
    <p class="agent__name">Marla Pembrook</p>
    <p class="agent__title">Realtor</p>
    <p class="agent__cell"><span class="icon-mobile"></span>(555).609.1385</p>
  </div>

  <ul class="office">
    <li>(555).240.3918
      <svg viewBox="0 0 13 13" aria-hidden="true"><rect width="13" height="13" rx="2" fill="#fff"/><path d="M3.5 3c.6-.5 1.2-.4 1.5.1l.7 1.2c.2.4 0 .8-.3 1l-.4.3c.4.9 1 1.5 1.9 1.9l.3-.4c.2-.3.6-.5 1-.3l1.2.7c.5.3.6.9.1 1.5-.7.8-1.700.8-2.8.2C5.4 8.4 4.6 7.6 3.8 6.3 3.2 5.2 2.8 3.9 3.5 3z" fill="#0d0d0d"/></svg>
    </li>
    <li>pembrook@hartwellestates-demo.com
      <svg viewBox="0 0 13 13" aria-hidden="true"><rect width="13" height="13" rx="2" fill="#fff"/><rect x="2.5" y="3.5" width="8" height="6" fill="#0d0d0d"/><path d="M2.5 3.5l4 3 4-3" stroke="#fff" stroke-width="0.9" fill="none"/></svg>
    </li>
    <li>www.hartwellestates-demo.com
      <svg viewBox="0 0 13 13" aria-hidden="true"><rect width="13" height="13" rx="2" fill="#fff"/><circle cx="6.5" cy="6.5" r="4" fill="#0d0d0d"/><path d="M2.5 6.5h8M6.5 2.5c-1.6 2-1.6 6 0 8M6.5 2.5c1.6 2 1.6 6 0 8" stroke="#fff" stroke-width="0.7" fill="none"/></svg>
    </li>
  </ul>
</section>

<section class="card card--back" aria-label="Card back">
  <div class="brand">
    <span class="brand__dot"></span>
    <span class="brand__words">
      <span class="brand__name">HARTWELL</span>
      <span class="brand__rule"></span>
      <span class="brand__sub">Estates</span>
    </span>
  </div>
  <p class="address">418B W. Calloway Ave.Calder Springs, OK. 70913</p>
</section>

</body>
</html>
```